Young, dynamic furniture company needs a new business card design

We require a new business card design for our modern furniture company which supplies furniture and appliances to the property and development market.
Oakridge Interiors has become one of the leading furniture & appliance suppliers to the property market withing London. With over 10 years experience, we have increased our business to supply not only private landlords and managing agents, but also property developers, housing associations and local councils.
We offer not only a complete range of furniture which includes beds, wardrobes, dining sets and sofas, but also a high quality, full delivery and assembly service to help you with all our furnishing needs.

Target Market(s)

Private landlords, estate agents, letting agents, property management companies

Industry/Entity Type

Business

Contact Information for Business Card

Name,
Title,
Address,
Mobile,
Telephone,
Fax, Website, email address

Font styles to use
Sans Serif

Colors
3176b5
0555a3
85abd2
cfdeed

Requirements
Must have
• All the above information for each of our staff, along with our logo

```html
<!DOCTYPE html>
<html lang="en">
<head>
<meta charset="utf-8">
<title>Oakridge Interiors – Business Card</title>
<link rel="stylesheet" href="https://fonts.googleapis.com/css2?family=Lato:wght@400;700&display=swap">
<style>
  :root {
    --brand-blue: #3176b5;
    --brand-deep: #0555a3;
    --brand-light: #85abd2;
    --brand-pale: #cfdeed;
    --ink: #1a1a1a;
    --paper: #ffffff;
    --backdrop: #e9ecef;
  }
  * { box-sizing: border-box; margin: 0; padding: 0; }
  html, body { width: 1200px; height: 900px; overflow: hidden; }
  body {
    background: var(--backdrop);
    font-family: "Lato", Arial, sans-serif;
    position: relative;
  }
  .card {
    position: absolute;
    width: 680px;
    height: 390px;
    border-radius: 3px;
    box-shadow: 0 6px 18px rgba(0,0,0,0.18);
    overflow: hidden;
  }
  /* Reverse side */
  .card--back {
    left: 440px; top: 40px;
    background: var(--brand-blue);
    color: var(--paper);
    display: flex; flex-direction: column; align-items: center; justify-content: center;
    text-align: center;
  }
  .brand {
    display: flex; align-items: center; gap: 14px;
  }
  .brand__mark {
    width: 34px; height: 34px; background: currentColor;
  }
  .brand__name {
    font-size: 34px; font-weight: 400; letter-spacing: 0.5px; text-transform: uppercase;
  }
  .brand__tagline {
    font-size: 14px; letter-spacing: 1px; text-transform: uppercase; margin-top: 6px;
  }
  .card--back .website {
    font-size: 20px; letter-spacing: 2px; margin-top: 28px;
  }
  /* Front side */
  .card--front {
    left: 80px; top: 470px;
    background: var(--paper);
    color: var(--ink);
  }
  .front__brand {
    position: absolute; left: 44px; top: 40px; color: var(--ink);
  }
  .front__brand .brand__name { font-size: 26px; }
  .front__brand .brand__mark { width: 26px; height: 26px; background: var(--brand-deep); }
  .front__brand .brand__tagline { font-size: 11px; color: #444; }
  .address {
    position: absolute; left: 44px; top: 130px;
    font-size: 18px; line-height: 1.3;
  }
  .contacts {
    position: absolute; left: 44px; top: 196px;
    list-style: none; font-size: 17px; line-height: 1.45;
  }
  .contacts li { display: flex; align-items: center; gap: 10px; }
  .contacts svg { width: 14px; height: 14px; fill: var(--brand-deep); flex: none; }
  .person {
    position: absolute; right: 50px; top: 240px; text-align: right;
  }
  .person__name { font-size: 34px; color: var(--brand-deep); font-weight: 400; }
  .person__title { font-size: 20px; color: var(--ink); }
  .band { position: absolute; left: 0; bottom: 0; width: 680px; height: 70px; }
  .card--front .website {
    position: absolute; right: 36px; bottom: 10px;
    color: var(--paper); font-size: 20px; letter-spacing: 1px;
  }
</style>
</head>
<body>
  <section class="card card--back">
    <div class="brand">
      <span class="brand__mark"></span>
      <span class="brand__name">Oakridge Interiors</span>
    </div>
    <p class="brand__tagline">Trade Furniture Solutions</p>
    <p class="website">www.trade.oakridgeint.co.uk</p>
  </section>

  <section class="card card--front">
    <div class="front__brand">
      <div class="brand">
        <span class="brand__mark"></span>
        <span class="brand__name">Oakridge Interiors</span>
      </div>
      <p class="brand__tagline">Trade Furniture Solutions</p>
    </div>

    <p class="address">27B Elmfield Trade Park<br>North Finchley, London</p>

    <ul class="contacts">
      <li><svg viewBox="0 0 24 24"><path d="M6.6 10.8a15 15 0 0 0 6.6 6.6l2.2-2.2a1 1 0 0 1 1-.25 11.4 11.4 0 0 0 3.6.57 1 1 0 0 1 1 1V20a1 1 0 0 1-1 1A17 17 0 0 1 3 4a1 1 0 0 1 1-1h3.5a1 1 0 0 1 1 1c0 1.25.2 2.45.57 3.57a1 1 0 0 1-.25 1z"/></svg>020 7946 0321</li>
      <li><svg viewBox="0 0 24 24"><path d="M7 1h10a2 2 0 0 1 2 2v18a2 2 0 0 1-2 2H7a2 2 0 0 1-2-2V3a2 2 0 0 1 2-2zm0 4v13h10V5z"/></svg>020 7946 0000</li>
      <li><svg viewBox="0 0 24 24"><path d="M2 5h20v14H2zm2 2v.5l8 5 8-5V7zm0 3v7h16v-7l-8 5z"/></svg>info@trade.oakridgeint.co.uk</li>
    </ul>

    <div class="person">
      <p class="person__name">Daniel Hartley</p>
      <p class="person__title">Manager</p>
    </div>

    <svg class="band" viewBox="0 0 680 70" preserveAspectRatio="none" aria-hidden="true">
      <path d="M0 22 L300 22 C322 22 322 36 344 36" fill="none" stroke="var(--brand-light)" stroke-width="5"/>
      <path d="M0 52 L310 52 C330 52 332 26 356 26 L680 26 L680 70 L0 70 Z" fill="var(--brand-blue)"/>
    </svg>
    <p class="website">www.trade.oakridgeint.co.uk</p>
  </section>
</body>
</html>
```